1 Dimensional cover for digital product

Please note that if a designer comes in with an original design and other designers try to copy them too closely I will always work with the original designer in order to get the actual look I want.
Therefore it is in the interests of the designers to get their concepts in first.

I am designing some audio products for football (soccer players).

I would like a square version and a 16:9 version of the packaging completed. The square version will be for the Sonvia audio cover and the 16:9 for the thumbnails of videos.

I would like the final images in PSP files as a template that I can change the title and the main image.

I am open to creativity in this project but would like it to be a luxury and premium in what it is portraying.

I have added my logo and also the packaging that I currently use on my sister website which is not aimed at football, soccer.

I've also included an image of one of my models. This would NOT be the product image, but it could be a background image, or you may choose to leave it out altogether.

I've also included an example image as the main product image.

Although I have chosen greyscale I would also like to see products with colour.

The product page is at https://kelvarn.global/collections/all
I add this so that you can chose any one of the titles for this template

Target Market(s)

This is aimed at professional footballers

Industry/Entity Type

Sporting Good

Font styles to use
Serif
Sans Serif

Colors

Designer to choose colors to be used in the design.

Requirements
Must have
• This must look like it is made for an affluent market.
• It may also be simple in its design but I do not wish to be too prescriptive with creativity.
• My typography is Montserrat
Nice to have
• Can include the colors of my logos:
• #5BA9DE
• #272B5F
• Or you can choose to go with greyscale
Should not have
• This is a product for serious athletes so it should look very professional and adult orientated (so not cartoonish its look)

```html
<!DOCTYPE html>
<html lang="en">
<head>
<meta charset="utf-8">
<title>Attacking Vision – Hypnosis Sessions</title>
<link href="https://fonts.googleapis.com/css2?family=Montserrat:wght@300;400;500;800&display=swap" rel="stylesheet">
<style>
  :root {
    --gold: #b5a766;
    --blue-edge: #1899c6;
    --blue-bright: #15b5e1;
    --blue-mid: #1494c1;
    --navy: #0b3549;
    --navy-strip: #0f4a61;
    --frame-outer: #137fae;
    --frame-inner: #1aa6d4;
    --ink: #2a2f6a;
    --white: #ffffff;
  }
  * { margin: 0; padding: 0; box-sizing: border-box; }
  html, body {
    width: 1200px; height: 675px; overflow: hidden;
    background: #ffffff;
  }
  .cover {
    position: relative;
    width: 1200px; height: 675px;
    overflow: hidden;
    font-family: "Montserrat", Arial, sans-serif;
    background: var(--gold);
  }
  .cover__backdrop {
    position: absolute; inset: 0;
  }
  .brand {
    position: absolute;
    left: 48px; top: 48px;
    width: 170px;
    display: flex; flex-direction: column; align-items: center;
    color: var(--white);
    font-weight: 400;
    font-size: 9.5px;
    letter-spacing: 0.3px;
    text-align: center;
    line-height: 1.35;
  }
  .brand__dot {
    width: 44px; height: 44px; border-radius: 50%;
    background: var(--white);
    margin-bottom: 10px;
  }
  .brand__sub { font-size: 12px; letter-spacing: 1.5px; }
  .eyebrow {
    position: absolute;
    left: 119px; top: 228px;
    color: var(--ink);
    font-weight: 500;
    font-size: 19px;
  }
  .title {
    position: absolute;
    left: 40px; top: 270px;
    width: 672px;
    color: var(--white);
    font-weight: 800;
    font-size: 112px;
    line-height: 0.86;
    letter-spacing: -1px;
    text-align: right;
    text-shadow: 4px 6px 10px rgba(0, 20, 40, 0.45);
  }
  .title span { display: block; }
  .title__first { text-align: left; }
  .benefit {
    position: absolute;
    left: 140px; top: 518px;
    display: flex; align-items: center; gap: 19px;
    color: var(--white);
    font-weight: 300;
    font-size: 13.5px;
    line-height: 1.25;
    text-transform: uppercase;
    letter-spacing: 0.3px;
  }
  .benefit__marker {
    width: 29px; height: 29px; border-radius: 50%;
    background: var(--gold);
    flex: none;
  }
</style>
</head>
<body>
  <main class="cover">
    <svg class="cover__backdrop" width="1200" height="675" viewBox="0 0 1200 675">
      <defs>
        <radialGradient id="arenaGlow" cx="0.55" cy="0.8" r="0.8">
          <stop offset="0" stop-color="#ece5b4"/>
          <stop offset="0.35" stop-color="#a49c6e"/>
          <stop offset="0.75" stop-color="#4b4a3d"/>
          <stop offset="1" stop-color="#2c2c26"/>
        </radialGradient>
      </defs>
      <path d="M0,170 C260,150 500,95 655,0 H1200 V675 H0 Z" fill="var(--blue-edge)"/>
      <path d="M0,196 C270,178 520,115 700,0 H1200 V675 H0 Z" fill="var(--blue-bright)"/>
      <path d="M0,318 C220,312 450,330 640,372 V675 H0 Z" fill="var(--blue-mid)"/>
      <path d="M0,404 C230,412 450,432 640,470 V675 H0 Z" fill="var(--navy)"/>
      <rect x="0" y="633" width="700" height="42" fill="var(--navy-strip)"/>
      <path d="M640,0 C565,170 555,480 660,675 H1200 V0 Z" fill="var(--frame-outer)"/>
      <path d="M668,0 C590,170 582,480 688,675 H1200 V0 Z" fill="var(--frame-inner)"/>
      <path class="hero-photo" role="img" aria-label="Two footballers leaping for the ball under stadium floodlights"
            d="M688,0 C610,170 604,480 712,675 H1200 V0 Z" fill="url(#arenaGlow)"/>
    </svg>

    <div class="brand">
      <div class="brand__dot"></div>
      <span>ELIAS TRENT HYPNOTHERAPY</span>
      <span class="brand__sub">KELVARN</span>
    </div>

    <p class="eyebrow">Hypnosis sessions</p>

    <h1 class="title">
      <span class="title__first">ATTACKING</span>
      <span class="title__second">VISION</span>
    </h1>

    <div class="benefit">
      <span class="benefit__marker"></span>
      <p>Improve your decision making<br>when you are attacking.</p>
    </div>
  </main>
</body>
</html>
```